Threat Lens ratings for Apps and Games

I need a web site designing that is aimed at parents and will show an "Threat Lens" rating for apps and games. I have attached a document with an overview of what the Threat Lens is. The website needs to be easy for parents to navigate and find what they want quickly and easily. I should also be able to update the website myself easily with "reviews" of the attack vectors for apps and games.

Target Market(s)

Parents

Coding

Coded - Design and coding required

Number of Pages Required

2 page

Requirements
Must have
• Clear and concise ratings for apps and games

```html
<!DOCTYPE html>
<html lang="en">
<head>
<meta charset="utf-8">
<title>Threat Lens ratings for Apps and Games</title>
<link rel="stylesheet" href="https://fonts.googleapis.com/css2?family=Montserrat:wght@400;500;600;700&family=Roboto:ital,wght@0,400;0,700;1,400&display=swap">
<style>
:root{
  --blue:#1a7fe6;
  --ink:#111111;
  --text:#555b63;
  --white:#ffffff;
  --line:#e6e8eb;
  --footer:#0b0b0b;
  --gold:#f5b400;
}
*{box-sizing:border-box;margin:0;padding:0}
html,body{width:1200px;height:5236px;overflow:hidden}
body{position:relative;background:var(--white);font-family:"Montserrat",sans-serif;color:var(--ink)}

/* header */
.site-header{position:absolute;left:0;top:0;width:1200px;height:79px;background:var(--white);border-bottom:1px solid var(--line)}
.brand{position:absolute;left:91px;top:16px;font-size:38px;font-weight:500;letter-spacing:.3px;color:var(--ink)}
.header-icons{position:absolute;right:80px;top:27px;display:flex;gap:30px}

/* hero */
.hero{position:absolute;left:0;top:79px;width:1200px;height:683px;
  background:linear-gradient(115deg,#e9d9cf 0%,#f1e3da 35%,#e7cfc1 60%,#cfc6c8 78%,#e9e6e8 100%)}
.hero-title{position:absolute;left:89px;top:214px;font-size:46px;font-weight:500;line-height:47px;color:var(--ink)}
.hero-lead{position:absolute;left:89px;top:323px;font-size:18px;line-height:27px;color:#222}
.btn{position:absolute;display:flex;align-items:center;justify-content:center;background:var(--blue);color:var(--white);font-weight:600;border-radius:30px}
.btn-hero{left:89px;top:403px;width:226px;height:57px;font-size:18px;box-shadow:0 4px 10px rgba(26,127,230,.35)}

/* features */
.feature-photo{position:absolute;width:459px;height:449px}
.round-tl{border-radius:200px 0 0 0}
.round-br{border-radius:0 0 200px 0}
.feature-title{position:absolute;font-size:46px;font-weight:500;line-height:47px;color:var(--ink);white-space:nowrap}
.accent{position:absolute;width:40px;height:5px;background:var(--blue);border-radius:2px}
.feature-text{position:absolute;width:447px;font-size:14.5px;line-height:26px;color:var(--text);text-align:justify}
.btn-more{width:175px;height:47px;font-size:15px}

/* rating */
.rating{position:absolute;left:0;top:3539px;width:1200px;height:607px;background:var(--blue)}
.rating-title{position:absolute;left:0;width:1200px;top:72px;text-align:center;font-size:46px;font-weight:500;color:var(--white)}
.rating .accent{background:var(--white);left:580px;top:153px}
.review{position:absolute;top:187px;width:328px}
.review-card{position:relative;height:187px;background:var(--white);border-radius:3px;padding:24px 40px 24px 26px;font-family:"Roboto",sans-serif;font-style:italic;font-size:13.5px;line-height:28px;color:#555}
.review-card::after{content:"";position:absolute;left:38px;bottom:-22px;border-left:19px solid transparent;border-right:19px solid transparent;border-top:23px solid var(--white)}
.reviewer{position:absolute;top:238px;left:0;width:328px;height:92px}
.avatar{position:absolute;left:0;top:0;width:92px;height:92px;border-radius:50%;border:3px solid var(--white)}
.reviewer-name{position:absolute;left:112px;top:24px;font-family:"Roboto",sans-serif;font-weight:700;font-size:17px;color:var(--white)}
.reviewer-role{position:absolute;left:112px;top:48px;font-family:"Roboto",sans-serif;font-style:italic;font-size:16px;color:#d8e9fb}
.stars{position:absolute;left:112px;top:72px;display:flex}

/* faq */
.faq-title{position:absolute;left:0;width:1200px;top:4224px;text-align:center;font-size:46px;font-weight:500;color:var(--ink)}
.faq .accent{left:580px;top:4301px}
.faq-item{position:absolute;left:146px;width:905px;height:78px;background:var(--white);box-shadow:0 2px 8px rgba(0,0,0,.09);padding:15px 18px;font-size:15.5px;line-height:23px;color:var(--text)}
.faq-item span{display:block;width:800px}
.btn-all{left:512px;top:4699px;width:175px;height:47px;font-size:15px}

/* footer */
.site-footer{position:absolute;left:0;top:4833px;width:1200px;height:403px;background:var(--footer);color:var(--white)}
.footer-brand{position:absolute;left:91px;top:56px;font-size:40px;font-weight:500}
.footer-about{position:absolute;left:91px;top:124px;width:397px;font-size:14px;line-height:22px;text-align:justify;color:#e8e8e8}
.footer-col{position:absolute;top:64px}
.footer-col h3{font-size:22px;font-weight:500;margin-bottom:14px}
.footer-col li{list-style:none;font-size:14px;line-height:26.5px;color:#e8e8e8}
.copyright{position:absolute;left:0;width:1200px;top:372px;text-align:center;font-size:13px;color:#e8e8e8}
</style>
</head>
<body>

<header class="site-header">
  <div class="brand">Threat Lens</div>
  <div class="header-icons">
    <svg width="20" height="20" viewBox="0 0 20 20" aria-label="Search"><circle cx="8" cy="8" r="5.5" fill="none" stroke="#777" stroke-width="2.2"/><line x1="12" y1="12" x2="17" y2="17" stroke="#777" stroke-width="2.4" stroke-linecap="round"/></svg>
    <svg width="20" height="20" viewBox="0 0 20 20" aria-label="Menu"><rect x="2" y="4" width="16" height="2.4" fill="#777"/><rect x="2" y="9" width="16" height="2.4" fill="#777"/><rect x="2" y="14" width="16" height="2.4" fill="#777"/></svg>
  </div>
</header>

<section class="hero" role="img" aria-label="Photo of a young child resting her head while touching a smartphone screen">
  <h1 class="hero-title">Threat Lens ratings<br>for Apps and Games</h1>
  <p class="hero-lead">Lorem ipsum dolor sit amet, consectetur adipiscing elit,<br>sed do eiusmod tempor incididunt ut labore</p>
  <a class="btn btn-hero">Get Started</a>
</section>

<div class="feature-photo round-tl" style="left:126px;top:854px;background:linear-gradient(135deg,#2f6f5d 0%,#c9a88c 45%,#ead9c8 70%,#dcd6cf 100%)" role="img" aria-label="Photo of a smiling girl with headphones holding a phone"></div>
<h2 class="feature-title" style="left:622px;top:908px">Login</h2>
<div class="accent" style="left:626px;top:980px"></div>
<p class="feature-text" style="left:626px;top:1006px">Lorem ipsum dolor sit amet, consectetur adipiscing elit, sed do eiusmod tempor incididunt ut labore et dolore magna aliqua. Ut enim ad minim veniam, quis nostrud exercitation ullamco laboris nisi ut aliquip ex ea commodo consequat. Duis aute irure dolor in reprehenderit in voluptate velit esse cillum dolore eu fugiat nulla pariatur.</p>
<a class="btn btn-more" style="left:626px;top:1195px">Read More</a>

<div class="feature-photo round-br" style="left:610px;top:1390px;background:linear-gradient(135deg,#d8cfc6 0%,#e9e3dc 40%,#2c3f8a 75%,#1f2f6e 100%)" role="img" aria-label="Photo of a boy looking at a smartphone on a sofa"></div>
<h2 class="feature-title" style="left:122px;top:1445px">Chat/Messaging</h2>
<div class="accent" style="left:126px;top:1517px"></div>
<p class="feature-text" style="left:126px;top:1543px">Lorem ipsum dolor sit amet, consectetur adipiscing elit, sed do eiusmod tempor incididunt ut labore et dolore magna aliqua. Ut enim ad minim veniam, quis nostrud exercitation ullamco laboris nisi ut aliquip ex ea commodo consequat. Duis aute irure dolor in reprehenderit in voluptate velit esse cillum dolore eu fugiat nulla pariatur.</p>
<a class="btn btn-more" style="left:126px;top:1731px">Read More</a>

<div class="feature-photo round-br" style="left:126px;top:1929px;background:linear-gradient(135deg,#e8e4df 0%,#a9856b 40%,#4f6f9a 70%,#d9d3cc 100%)" role="img" aria-label="Photo of a family on a sofa using a laptop and tablet"></div>
<h2 class="feature-title" style="left:622px;top:1983px">Camera/Microphone<br>Access</h2>
<div class="accent" style="left:626px;top:2080px"></div>
<p class="feature-text" style="left:626px;top:2106px">Lorem ipsum dolor sit amet, consectetur adipiscing elit, sed do eiusmod tempor incididunt ut labore et dolore magna aliqua. Ut enim ad minim veniam, quis nostrud exercitation ullamco laboris nisi ut aliquip ex ea commodo consequat.</p>
<a class="btn btn-more" style="left:626px;top:2269px">Read More</a>

<div class="feature-photo round-tl" style="left:610px;top:2465px;background:linear-gradient(135deg,#efeeec 0%,#d7cfc9 40%,#7e6a7c 70%,#cbb5b0 100%)" role="img" aria-label="Photo of a girl at a desk holding a phone and a pencil"></div>
<h2 class="feature-title" style="left:122px;top:2520px">Location Services</h2>
<div class="accent" style="left:126px;top:2592px"></div>
<p class="feature-text" style="left:126px;top:2618px">Lorem ipsum dolor sit amet, consectetur adipiscing elit, sed do eiusmod tempor incididunt ut labore et dolore magna aliqua. Ut enim ad minim veniam, quis nostrud exercitation ullamco laboris nisi ut aliquip ex ea commodo consequat. Duis aute irure dolor in reprehenderit in voluptate velit esse cillum dolore eu fugiat nulla pariatur.</p>
<a class="btn btn-more" style="left:126px;top:2806px">Read More</a>

<div class="feature-photo round-tl" style="left:126px;top:3004px;background:linear-gradient(135deg,#dcd2ca 0%,#b89a82 35%,#6f86a8 65%,#e6e2de 100%)" role="img" aria-label="Photo of a mother and daughter looking at a phone together"></div>
<h2 class="feature-title" style="left:622px;top:3058px">Live Streaming</h2>
<div class="accent" style="left:626px;top:3130px"></div>
<p class="feature-text" style="left:626px;top:3156px">Lorem ipsum dolor sit amet, consectetur adipiscing elit, sed do eiusmod tempor incididunt ut labore et dolore magna aliqua. Ut enim ad minim veniam, quis nostrud exercitation ullamco laboris nisi ut aliquip ex ea commodo consequat. Duis aute irure dolor in reprehenderit in voluptate velit esse cillum dolore eu fugiat nulla pariatur.</p>
<a class="btn btn-more" style="left:626px;top:3344px">Read More</a>

<section class="rating">
  <h2 class="rating-title">Customer Rating</h2>
  <div class="accent"></div>

  <div class="review" style="left:81px">
    <div class="review-card">Sed ut perspiciatis unde omnis iste natus error sit voluptatem accusantium doloremque laudantium, totam rem aperiam, eaque ipsa quae ab illo inventore veritatis et quasi architecto</div>
    <div class="reviewer">
      <div class="avatar" style="background:linear-gradient(160deg,#c9c3bd,#6c6a6a)" role="img" aria-label="Reviewer portrait"></div>
      <div class="reviewer-name">Jane Holt</div>
      <div class="reviewer-role">Lorem ipsum dolor</div>
      <div class="stars"><svg width="70" height="12" viewBox="0 0 70 12"><g fill="#f5b400"><circle cx="6" cy="6" r="4"/><circle cx="20" cy="6" r="4"/><circle cx="34" cy="6" r="4"/><circle cx="48" cy="6" r="4"/><circle cx="62" cy="6" r="4"/></g></svg></div>
    </div>
  </div>

  <div class="review" style="left:435px">
    <div class="review-card">Sed ut perspiciatis unde omnis iste natus error sit voluptatem accusantium doloremque laudantium, totam rem aperiam, eaque ipsa quae ab illo inventore veritatis et quasi architecto</div>
    <div class="reviewer">
      <div class="avatar" style="background:linear-gradient(160deg,#ede6df,#c9b29a)" role="img" aria-label="Reviewer portrait"></div>
      <div class="reviewer-name">Jane Holt</div>
      <div class="reviewer-role">Lorem ipsum dolor</div>
      <div class="stars"><svg width="70" height="12" viewBox="0 0 70 12"><g fill="#f5b400"><circle cx="6" cy="6" r="4"/><circle cx="20" cy="6" r="4"/><circle cx="34" cy="6" r="4"/><circle cx="48" cy="6" r="4"/><circle cx="62" cy="6" r="4"/></g></svg></div>
    </div>
  </div>

  <div class="review" style="left:789px">
    <div class="review-card">Sed ut perspiciatis unde omnis iste natus error sit voluptatem accusantium doloremque laudantium, totam rem aperiam, eaque ipsa quae ab illo inventore veritatis et quasi architecto</div>
    <div class="reviewer">
      <div class="avatar" style="background:linear-gradient(160deg,#bcc3cc,#3e4656)" role="img" aria-label="Reviewer portrait"></div>
      <div class="reviewer-name">Jane Holt</div>
      <div class="reviewer-role">Lorem ipsum dolor</div>
      <div class="stars"><svg width="70" height="12" viewBox="0 0 70 12"><g fill="#f5b400"><circle cx="6" cy="6" r="4"/><circle cx="20" cy="6" r="4"/><circle cx="34" cy="6" r="4"/><circle cx="48" cy="6" r="4"/><circle cx="62" cy="6" r="4"/></g></svg></div>
    </div>
  </div>
</section>

<section class="faq">
  <h2 class="faq-title">FAQ</h2>
  <div class="accent"></div>
  <div class="faq-item" style="top:4335px"><span>Does the game or app have access to the camera and mic and does the game/app have the ability to send pics or video within the app itself ?</span></div>
  <div class="faq-item" style="top:4424px"><span>Does the game or app have voice chat and can voice changing software interface into the game or app ?</span></div>
  <div class="faq-item" style="top:4513px"><span>Does the game or app have an inbuilt messaging service and what types of messages and content can be sent over this ?</span></div>
  <div class="faq-item" style="top:4602px"><span>Does it have any constraints on username such as length or whether you can use profanity on the user name ?</span></div>
  <a class="btn btn-all">View All</a>
</section>

<footer class="site-footer">
  <div class="footer-brand">Threat Lens</div>
  <p class="footer-about">Lorem ipsum dolor sit amet, consectetur adipiscing elit, sed do eiusmod tempor incididunt ut labore et dolore magna aliqua. Ut enim ad minim veniam, quis nostrud exercitation ullamco laboris nisi ut aliquip ex ea commodo consequat</p>
  <div class="footer-col" style="left:598px">
    <h3>Links</h3>
    <ul><li>Home</li><li>About Us</li><li>Services</li><li>FAQ</li><li>Rating</li><li>Contact Us</li></ul>
  </div>
  <div class="footer-col" style="left:768px">
    <h3>Others</h3>
    <ul><li>Blog</li><li>Privacy Policy</li><li>Terms &amp; Conditions</li></ul>
  </div>
  <div class="footer-col" style="left:996px">
    <h3>Follow Us</h3>
    <ul><li>Friendbook</li><li>Chirper</li><li>Snapgram</li><li>ViewTube</li></ul>
  </div>
  <div class="copyright">© 2021 The company Name. All rights Reserved.</div>
</footer>

</body>
</html>
```